New Business Card for Web Design/Internet Marketing Company

Looking for a great looking new business card. We are a 10 year old web design, internet marketing and website management company that works mostly with small businesses.

Our new card needs to better match the colors and style of our website, be bold, extremely usable and slightly edgy.

Target Market(s)

Small/Medium businesses that have websites

Industry/Entity Type

Internet

Requirements
Must have
• Front and back design, full color, rounded corners please

Must use the colors/style of our website (JPG provided)

INFO FOR CARDS (as readable as possible please)
Mark Lenner
President/CEO
mark@trelvanmedia.example
Phone: 520-381-7459
Toll Free: 866-381-7459
Address: 4315 W. Calloway Ave. Ste. 140, Tucson, AZ 85792

THINGS I WANT TO PROMOTE (if there is room):
1. Our Website - www.trelvanmedia.example

2. Social Media
Twitter: @trelvanmedia
Facebook: www.facebook.com/trelvanmedia

3. Our Services
Web Design
Internet Marketing
Website Management

```html
<!DOCTYPE html>
<html lang="en">
<head>
<meta charset="utf-8">
<title>Trelvan Media – Business Card</title>
<link href="https://fonts.googleapis.com/css2?family=PT+Sans:wght@400;700&family=PT+Sans+Narrow:wght@400;700&display=swap" rel="stylesheet">
<style>
  :root{
    --page:#eceef2;
    --sky:#1ea3dc;
    --sky-deep:#0e78b8;
    --navy:#0e4a8c;
    --navy-deep:#0a3c76;
    --sun:#ffd51c;
    --tangerine:#f7901e;
    --ice:#4fb6ea;
    --white:#ffffff;
    --ink-soft:#dff2fc;
  }
  *{box-sizing:border-box;margin:0;padding:0}
  html,body{width:1200px;height:900px;overflow:hidden}
  body{
    background:var(--page);
    font-family:"PT Sans",Arial,sans-serif;
    display:flex;align-items:center;justify-content:center;gap:60px;
  }
  .card{position:relative;border-radius:22px;overflow:hidden;box-shadow:0 10px 30px rgba(20,40,80,.18)}

  /* Front (portrait) */
  .card-front{
    width:380px;height:660px;
    background:linear-gradient(180deg,var(--sky) 0%,var(--sky-deep) 100%);
  }
  .front-tabs{position:absolute;top:0;left:28px;display:flex;gap:12px}
  .front-tab{width:92px;height:16px;background:linear-gradient(90deg,var(--sun),var(--tangerine));border-radius:0 0 6px 6px}
  .contact{position:absolute;left:34px;right:30px;top:54px;color:var(--white)}
  .person-name{font-size:40px;line-height:1;font-weight:400;color:var(--white)}
  .person-name .first{color:var(--tangerine);font-weight:700}
  .person-title{font-family:"PT Sans Narrow",sans-serif;font-size:13px;letter-spacing:2px;color:var(--ink-soft);margin-top:8px}
  .address{font-size:14px;line-height:1.4;margin-top:20px}
  .contact-list{list-style:none;margin-top:18px;display:flex;flex-direction:column;gap:12px}
  .contact-list li{display:flex;align-items:center;gap:10px;font-size:15px}
  .contact-dot{width:13px;height:13px;border-radius:50%;background:var(--ink-soft);flex:none}
  .toll-free{
    background:linear-gradient(90deg,var(--sun),var(--tangerine));color:var(--navy);
    font-weight:700;font-size:17px;padding:4px 12px;border-radius:6px;white-space:nowrap;
  }
  .brand-band{
    position:absolute;left:0;bottom:0;width:100%;height:150px;
    background:linear-gradient(90deg,var(--tangerine) 0%,var(--sun) 100%);
    display:flex;flex-direction:column;align-items:center;justify-content:center;gap:6px;
  }
  .brand-band .brand-name{color:var(--navy);font-weight:700;font-size:38px;letter-spacing:.5px}
  .brand-band .brand-tagline{color:var(--navy);font-size:14px;letter-spacing:1px}

  /* Back (landscape) */
  .card-back{width:660px;height:380px;background:linear-gradient(160deg,var(--navy) 0%,var(--navy-deep) 100%)}
  .corner-swoosh{position:absolute;inset:0;width:100%;height:100%}
  .back-content{position:absolute;inset:0;display:flex;flex-direction:column;align-items:center;justify-content:center}
  .back-logo{display:flex;align-items:center;gap:12px}
  .back-logo .brand-mark{width:24px;height:24px;border-radius:50%;background:var(--tangerine)}
  .back-logo .brand-name{color:var(--ice);font-weight:700;font-size:50px;letter-spacing:.5px}
  .back-tagline{color:var(--ice);font-size:16px;margin-top:2px}
  .services{
    margin-top:16px;background:var(--ice);color:var(--navy-deep);font-weight:700;font-size:15px;
    padding:6px 18px;border-radius:6px;display:flex;gap:10px;
  }
  .services .divider{opacity:.6}
  .social{margin-top:16px;display:flex;gap:26px;color:var(--white);font-size:14px}
  .social span{display:flex;align-items:center;gap:8px}
  .social-dot{width:12px;height:12px;border-radius:50%;background:var(--tangerine)}
</style>
</head>
<body>

  <section class="card card-front" aria-label="Business card front">
    <div class="front-tabs"><span class="front-tab"></span><span class="front-tab"></span></div>
    <div class="contact">
      <h1 class="person-name"><span class="first">MARK</span> Lenner</h1>
      <p class="person-title">PRESIDENT/CEO</p>
      <p class="address">4315 W. Calloway Ave. Ste. 140<br>Tucson, AZ 85792</p>
      <ul class="contact-list">
        <li><span class="contact-dot"></span>520-381-7459</li>
        <li><span class="contact-dot"></span><span class="toll-free">866-381-7459 (Toll Free)</span></li>
        <li><span class="contact-dot"></span>mark@trelvanmedia.example</li>
        <li><span class="contact-dot"></span>www.trelvanmedia.example</li>
      </ul>
    </div>
    <div class="brand-band">
      <span class="brand-name">Trelvan Media</span>
      <span class="brand-tagline">Sites that work harder</span>
    </div>
  </section>

  <section class="card card-back" aria-label="Business card back">
    <svg class="corner-swoosh" viewBox="0 0 660 380" preserveAspectRatio="none" aria-hidden="true">
      <defs>
        <linearGradient id="swoosh" x1="0" y1="0" x2="1" y2="1">
          <stop offset="0" stop-color="#ffd51c"/>
          <stop offset="1" stop-color="#f7901e"/>
        </linearGradient>
      </defs>
      <path d="M0 0 H70 Q20 30 0 90 Z" fill="url(#swoosh)"/>
      <path d="M660 380 H580 Q645 310 660 205 Z" fill="url(#swoosh)"/>
    </svg>
    <div class="back-content">
      <div class="back-logo"><span class="brand-mark"></span><span class="brand-name">Trelvan Media</span></div>
      <p class="back-tagline">Sites that work harder</p>
      <p class="services"><span>Web Design</span><span class="divider">|</span><span>Internet Marketing</span><span class="divider">|</span><span>Website Management</span></p>
      <p class="social">
        <span><i class="social-dot"></i>www.trelvanmedia.example/social</span>
        <span><i class="social-dot"></i>@trelvanmedia</span>
      </p>
    </div>
  </section>

</body>
</html>
```